wordpress website Carla Winfield, Author, Speaker and Coach

Need a wordpress blogging website for author/speaker/coach.
I have paid for hosting on nestparrot.
I am currently writing a book - Launchpad to Campus - Steps and strategies to prepare you to thrive in college and beyond. Eventually, I will have an Academic/Life Coaching program targeting high school and college students. This website's purpose is to build my email list. I can offer the following reports as incentive for email sign-up:
1. Six Habits That Get Your Teen Through University On Schedule and Debt-Light
2. Surprising Routes to Fund Your Degree
3. SAT/ACT vocabulary word of the day

facebook page: https://www.facebook.com/Carla-Winfield-AcademicLife-Coach-918273645501928/

I would like to have these pages:

1. Home or About page

High school is becoming more and more stressful for students. Not only are they taking more AP classes than ever before, and often spending $1,000’s on SAT/ACT prep programs, most are NOT prepared for success in college. Only 19% of students are graduating from college within 4 years and only 56% are graduating within 6 years. With the cost of higher education skyrocketing, each extra year of school can costs families $40,000 - $60,000 when you factor in living expenses. Then, when students do graduate, they are often underemployed.

Carla's approach is whole person oriented. Her programs help students learn life skills in addition to the study, time management skills, etc. offered by most academic coaching programs. Our program addresses all of the major causes of failure to graduate within 4 years, and is based on sound educational research. Carla's program initially provides the daily interaction needed to successfully change behaviors and seat new success habits, unlike many programs in which students interact with coaches only once a week.
Bio
Carla Winfield is a certified teacher and holds advanced certification in academic coaching and tutoring. She also is a certified trainer in the Morris Tellwright Achievement Keys. She has three successful adult children, and helped them overcome learning differences and thrive.

2. Blog

3. Contact - Include form (I split time between USA and Saudi Arabia, so I will call or email people back, but don't want to leave a phone number)
info@carlawinfield.example

4. Store – 1 book for now
Launchpad to Campus
Steps and strategies to prepare you to thrive in college and beyond
Available 12/01/2017
I could make a preview chapter available for download

5. Speaking
Carla Winfield is available for keynote addresses and half-day, full day or multi-day workshops. I will develop details later

6.Coaching programs
I will develop details later

Target Market(s)

high school students who are college bound and their parents

Number of Pages Required

5+ page

Font styles to use
Sans Serif

Colors

Designer to choose colors to be used in the design.

Requirements
Nice to have
• integration with post finch for contact management

```html
<!DOCTYPE html>
<html lang="en">
<head>
<meta charset="utf-8">
<title>Carla Winfield — Author, Speaker and Coach</title>
<link rel="stylesheet" href="https://fonts.googleapis.com/css2?family=Lato:wght@400;700&family=Open+Sans:wght@400;600&display=swap">
<style>
:root{
  --ink:#1f1f1f;
  --text:#666666;
  --nav:#333333;
  --green:#8cc540;
  --purple:#8a8bc8;
  --purple-dark:#7576b6;
  --white:#ffffff;
  --footer:#333333;
  --footer-line:#8a8a8a;
}
*{box-sizing:border-box;margin:0;padding:0}
html,body{width:1200px;height:2571px;overflow:hidden}
body{position:relative;background:var(--white);font-family:"Open Sans",Arial,sans-serif;color:var(--text)}
.abs{position:absolute}
.icon{display:inline-block;vertical-align:middle}

/* header */
.site-header{left:0;top:0;width:1200px;height:94px;background:var(--white)}
.brand{left:99px;top:34px;display:flex;align-items:center;gap:10px;font-family:"Lato",Arial,sans-serif;font-size:19px;font-weight:700;color:var(--purple-dark);letter-spacing:.5px}
.brand-dot{width:22px;height:22px;border-radius:50%;background:var(--green)}
.main-nav{right:99px;top:36px;display:flex;gap:27px;font-size:14.5px;color:var(--nav);text-transform:uppercase;letter-spacing:.3px}

/* hero */
.hero{left:0;top:94px;width:1200px;height:477px;
  background:
    radial-gradient(ellipse 420px 260px at 24% 18%,rgba(246,244,214,.85) 0%,rgba(246,244,214,0) 70%),
    radial-gradient(ellipse 300px 320px at 78% 48%,rgba(236,232,222,.55) 0%,rgba(236,232,222,0) 70%),
    linear-gradient(180deg,#9fbf78 0%,#6f9a48 38%,#5f8a3c 62%,#86b255 80%,#a9cc72 100%)}
.hero-title{left:99px;top:250px;font-family:"Lato",Arial,sans-serif;font-size:31px;font-weight:700;line-height:42px;color:var(--white);text-transform:uppercase;text-shadow:0 1px 3px rgba(0,0,0,.25)}
.hero-dots{left:99px;top:501px;display:flex;gap:11px}
.hero-dots span{width:20px;height:20px;border-radius:50%;background:var(--white)}
.hero-dots span.active{background:var(--purple-dark)}

/* about */
.portrait{left:100px;top:670px;width:310px;height:310px;border-radius:50%;border:4px solid var(--white);box-shadow:0 0 0 2px #dddddd;
  background:
    radial-gradient(ellipse 90px 110px at 50% 42%,#d8a891 0%,rgba(216,168,145,0) 100%),
    radial-gradient(ellipse 130px 90px at 50% 92%,#111 0%,rgba(17,17,17,0) 100%),
    linear-gradient(135deg,#6b3a2e 0%,#3a2522 50%,#1a1414 100%)}
.about-title{left:495px;top:725px;font-family:"Lato",Arial,sans-serif;font-size:26px;font-weight:700;color:var(--ink)}
.about-text{left:495px;top:782px;width:606px;font-size:12px;line-height:21px;color:var(--text)}
.btn-read{left:495px;top:874px;width:141px;height:50px;border-radius:4px;background:var(--green);color:var(--white);font-size:14.5px;font-weight:600;text-transform:uppercase;display:flex;align-items:center;justify-content:center}

/* purpose */
.purpose{left:0;top:1083px;width:1200px;height:431px;background:var(--purple)}
.purpose-title{left:99px;top:1164px;font-family:"Lato",Arial,sans-serif;font-size:25px;font-weight:700;color:var(--white);text-transform:uppercase}
.purpose-lead{left:99px;top:1221px;font-size:19px;font-weight:600;color:var(--white)}
.report-list{left:99px;top:1269px;list-style:none;font-size:11.5px;color:var(--white)}
.report-list li{display:flex;align-items:center;gap:12px;height:26px}
.signup{left:99px;top:1381px;width:365px;height:46px;border:2px solid var(--white);display:flex}
.signup-field{flex:1;display:flex;align-items:center;padding-left:18px;font-size:11.5px;color:var(--white)}
.signup-send{width:54px;background:var(--green);display:flex;align-items:center;justify-content:center}
.seal{left:780px;top:1145px;width:305px;height:305px;border-radius:50%;
  background:radial-gradient(circle at 40% 35%,#f6f6f6 0%,#d2d2d2 50%,#a2a2a2 100%);
  box-shadow:0 4px 10px rgba(0,0,0,.22), inset 0 0 0 14px rgba(255,255,255,.35), inset 0 0 0 16px rgba(120,120,120,.35)}

/* blog */
.blog-title{left:0;top:1605px;width:1200px;text-align:center;font-family:"Lato",Arial,sans-serif;font-size:26px;font-weight:700;color:var(--ink);text-transform:uppercase}
.blog-sub{left:0;top:1649px;width:1200px;text-align:center;font-size:11.5px;color:var(--text)}
.post{top:1731px;width:305px}
.post-photo{position:relative;height:186px;box-shadow:0 6px 8px -4px rgba(0,0,0,.35)}
.post-actions{position:absolute;right:18px;bottom:12px;display:flex;gap:16px;font-size:11.5px;color:var(--white)}
.post-actions span{display:flex;align-items:center;gap:5px}
.post-title{margin-top:38px;font-family:"Lato",Arial,sans-serif;font-size:15px;font-weight:700;color:var(--ink);text-transform:uppercase;letter-spacing:.3px;white-space:nowrap}
.post-meta{margin-top:16px;font-size:11px;color:var(--text);display:flex;gap:12px}
.post-meta span{display:flex;align-items:center;gap:6px}
.post-excerpt{margin-top:14px;font-size:11px;line-height:21px;color:var(--text)}

/* footer */
.site-footer{left:0;top:2155px;width:1200px;height:416px;background:var(--footer)}
.footer-brand{left:0;top:2280px;width:1200px;display:flex;justify-content:center;align-items:center;gap:10px;font-family:"Lato",Arial,sans-serif;font-size:19px;font-weight:700;color:var(--white);letter-spacing:.5px}
.footer-nav{left:0;top:2341px;width:1200px;display:flex;justify-content:center;gap:38px;font-size:12.5px;font-weight:600;color:var(--white)}
.social{left:0;top:2393px;width:1200px;display:flex;justify-content:center;gap:11px}
.social span{width:48px;height:48px;border-radius:50%;border:2px solid var(--white);display:flex;align-items:center;justify-content:center}
.footer-rule{left:99px;top:2485px;width:1002px;height:1px;background:var(--footer-line)}
.copyright{left:0;top:2521px;width:1200px;text-align:center;font-size:12.5px;color:var(--white)}
</style>
</head>
<body>

<header class="abs site-header">
  <div class="abs brand"><span class="brand-dot"></span>CARLA WINFIELD</div>
  <nav class="abs main-nav"><span>Home</span><span>Blog</span><span>Store</span><span>Speaking</span><span>Coaching Program</span><span>Contact</span></nav>
</header>

<section class="abs hero" role="img" aria-label="Young woman in glasses reading a book while sitting on the grass in a sunny park"></section>
<h1 class="abs hero-title">Steps and strategies to prepare<br>you to thrive in college</h1>
<div class="abs hero-dots"><span></span><span class="active"></span><span></span></div>

<div class="abs portrait" role="img" aria-label="Portrait of Carla Winfield"></div>
<h2 class="abs about-title">ABOUT US</h2>
<p class="abs about-text">High school is becoming more and more stressful for students. Not only are they taking more AP classes than ever before, and often spending $1,000’s on SAT/ACT prep programs, most are NOT prepared for success in college. Only 19% of students are graduating from college</p>
<div class="abs btn-read">Read More</div>

<section class="abs purpose"></section>
<h2 class="abs purpose-title">Our Purpose</h2>
<p class="abs purpose-lead">I can offer the following reports as incentive for email sign-up:</p>
<ul class="abs report-list">
  <li><svg class="icon" width="11" height="11" viewBox="0 0 11 11"><path d="M1 10 L10 1 M6 1 H10 V5" stroke="#fff" stroke-width="1.6" fill="none"/></svg>Six Habits That Get Your Teen Through University On Schedule and Debt-Light</li>
  <li><svg class="icon" width="11" height="11" viewBox="0 0 11 11"><path d="M1 10 L10 1 M6 1 H10 V5" stroke="#fff" stroke-width="1.6" fill="none"/></svg>Surprising Routes to Fund Your Degree</li>
  <li><svg class="icon" width="11" height="11" viewBox="0 0 11 11"><path d="M1 10 L10 1 M6 1 H10 V5" stroke="#fff" stroke-width="1.6" fill="none"/></svg>SAT/ACT vocabulary word of the day</li>
</ul>
<div class="abs signup">
  <div class="signup-field">Enter your mail</div>
  <div class="signup-send"><svg width="24" height="22" viewBox="0 0 24 22"><path d="M1 10 L23 1 L17 21 L11 13 Z M11 13 L23 1" fill="#fff" stroke="#8cc540" stroke-width="1"/></svg></div>
</div>
<div class="abs seal" role="img" aria-label="Certified trainer seal"></div>

<h2 class="abs blog-title">Latest Blog Post</h2>
<p class="abs blog-sub">It is a long established fact that a reader will be looking at its layout</p>

<article class="abs post" style="left:101px">
  <div class="post-photo" role="img" aria-label="Students working at desks in a classroom" style="background:radial-gradient(ellipse 120px 80px at 30% 20%,rgba(240,240,236,.9) 0%,rgba(240,240,236,0) 100%),radial-gradient(ellipse 90px 120px at 90% 60%,rgba(40,90,190,.7) 0%,rgba(40,90,190,0) 100%),linear-gradient(180deg,#d9d6cf 0%,#a08b7c 55%,#6d6a6a 100%)">
    <div class="post-actions"><span><svg class="icon" width="11" height="10" viewBox="0 0 11 10"><path d="M5.5 9.5 L1 5 A2.4 2.4 0 0 1 5.5 1.8 A2.4 2.4 0 0 1 10 5 Z" fill="#fff"/></svg>Likes</span><span><svg class="icon" width="10" height="10" viewBox="0 0 10 10"><circle cx="8" cy="2" r="1.6" fill="#fff"/><circle cx="2" cy="5" r="1.6" fill="#fff"/><circle cx="8" cy="8" r="1.6" fill="#fff"/><path d="M8 2 L2 5 L8 8" stroke="#fff" stroke-width="1" fill="none"/></svg>Share</span></div>
  </div>
  <h3 class="post-title">Eiusmod tempor incidunt ipsumdol</h3>
  <div class="post-meta"><span><svg class="icon" width="9" height="10" viewBox="0 0 9 10"><circle cx="4.5" cy="3" r="2.5" fill="#666"/><path d="M0 10 A4.5 4.5 0 0 1 9 10 Z" fill="#666"/></svg>by Jhon,</span><span><svg class="icon" width="10" height="10" viewBox="0 0 10 10"><rect x="0.5" y="1.5" width="9" height="8" fill="none" stroke="#666"/><rect x="0.5" y="1.5" width="9" height="2.5" fill="#666"/></svg>March 2017,</span><span><svg class="icon" width="11" height="10" viewBox="0 0 11 10"><ellipse cx="5.5" cy="4.5" rx="5" ry="3.8" fill="#666"/><path d="M2 7 L1 10 L5 8" fill="#666"/></svg>0 Comments</span></div>
  <p class="post-excerpt">Lorem ipsum dolor sit amet, consectetur adipisici elit, sed eiusmod tempor incidunt ut labore here.......</p>
</article>
<article class="abs post" style="left:446px">
  <div class="post-photo" role="img" aria-label="Student writing at a library table" style="background:radial-gradient(ellipse 110px 90px at 90% 20%,rgba(140,70,50,.8) 0%,rgba(140,70,50,0) 100%),radial-gradient(ellipse 100px 70px at 50% 90%,rgba(225,215,195,.7) 0%,rgba(225,215,195,0) 100%),linear-gradient(180deg,#5a3e33 0%,#3c3a5c 55%,#2c3666 100%)">
    <div class="post-actions"><span><svg class="icon" width="11" height="10" viewBox="0 0 11 10"><path d="M5.5 9.5 L1 5 A2.4 2.4 0 0 1 5.5 1.8 A2.4 2.4 0 0 1 10 5 Z" fill="#fff"/></svg>Likes</span><span><svg class="icon" width="10" height="10" viewBox="0 0 10 10"><circle cx="8" cy="2" r="1.6" fill="#fff"/><circle cx="2" cy="5" r="1.6" fill="#fff"/><circle cx="8" cy="8" r="1.6" fill="#fff"/><path d="M8 2 L2 5 L8 8" stroke="#fff" stroke-width="1" fill="none"/></svg>Share</span></div>
  </div>
  <h3 class="post-title">Eiusmod tempor incidunt ipsumdol</h3>
  <div class="post-meta"><span><svg class="icon" width="9" height="10" viewBox="0 0 9 10"><circle cx="4.5" cy="3" r="2.5" fill="#666"/><path d="M0 10 A4.5 4.5 0 0 1 9 10 Z" fill="#666"/></svg>by Jhon,</span><span><svg class="icon" width="10" height="10" viewBox="0 0 10 10"><rect x="0.5" y="1.5" width="9" height="8" fill="none" stroke="#666"/><rect x="0.5" y="1.5" width="9" height="2.5" fill="#666"/></svg>March 2017,</span><span><svg class="icon" width="11" height="10" viewBox="0 0 11 10"><ellipse cx="5.5" cy="4.5" rx="5" ry="3.8" fill="#666"/><path d="M2 7 L1 10 L5 8" fill="#666"/></svg>0 Comments</span></div>
  <p class="post-excerpt">Lorem ipsum dolor sit amet, consectetur adipisici elit, sed eiusmod tempor incidunt ut labore here.......</p>
</article>
<article class="abs post" style="left:792px">
  <div class="post-photo" role="img" aria-label="Teacher speaking to a class at a whiteboard" style="background:radial-gradient(ellipse 90px 90px at 10% 80%,rgba(190,50,45,.85) 0%,rgba(190,50,45,0) 100%),radial-gradient(ellipse 140px 80px at 60% 25%,rgba(245,245,245,.9) 0%,rgba(245,245,245,0) 100%),linear-gradient(180deg,#dedede 0%,#b3b3b6 55%,#77767a 100%)">
    <div class="post-actions"><span><svg class="icon" width="11" height="10" viewBox="0 0 11 10"><path d="M5.5 9.5 L1 5 A2.4 2.4 0 0 1 5.5 1.8 A2.4 2.4 0 0 1 10 5 Z" fill="#fff"/></svg>Likes</span><span><svg class="icon" width="10" height="10" viewBox="0 0 10 10"><circle cx="8" cy="2" r="1.6" fill="#fff"/><circle cx="2" cy="5" r="1.6" fill="#fff"/><circle cx="8" cy="8" r="1.6" fill="#fff"/><path d="M8 2 L2 5 L8 8" stroke="#fff" stroke-width="1" fill="none"/></svg>Share</span></div>
  </div>
  <h3 class="post-title">Eiusmod tempor incidunt ipsumdol</h3>
  <div class="post-meta"><span><svg class="icon" width="9" height="10" viewBox="0 0 9 10"><circle cx="4.5" cy="3" r="2.5" fill="#666"/><path d="M0 10 A4.5 4.5 0 0 1 9 10 Z" fill="#666"/></svg>by Jhon,</span><span><svg class="icon" width="10" height="10" viewBox="0 0 10 10"><rect x="0.5" y="1.5" width="9" height="8" fill="none" stroke="#666"/><rect x="0.5" y="1.5" width="9" height="2.5" fill="#666"/></svg>March 2017,</span><span><svg class="icon" width="11" height="10" viewBox="0 0 11 10"><ellipse cx="5.5" cy="4.5" rx="5" ry="3.8" fill="#666"/><path d="M2 7 L1 10 L5 8" fill="#666"/></svg>0 Comments</span></div>
  <p class="post-excerpt">Lorem ipsum dolor sit amet, consectetur adipisici elit, sed eiusmod tempor incidunt ut labore here.......</p>
</article>

<footer class="abs site-footer"></footer>
<div class="abs footer-brand"><span class="brand-dot"></span>CARLA WINFIELD</div>
<nav class="abs footer-nav"><span>Home</span><span>Blog</span><span>Store</span><span>Speaking</span><span>Coaching Program</span><span>Contact</span></nav>
<div class="abs social">
  <span aria-label="Share"><svg width="18" height="18" viewBox="0 0 18 18"><circle cx="14" cy="4" r="2.6" fill="#fff"/><circle cx="4" cy="9" r="2.6" fill="#fff"/><circle cx="14" cy="14" r="2.6" fill="#fff"/><path d="M14 4 L4 9 L14 14" stroke="#fff" stroke-width="1.6" fill="none"/></svg></span>
  <span aria-label="Website"><svg width="18" height="18" viewBox="0 0 18 18"><circle cx="9" cy="9" r="7.5" fill="none" stroke="#fff" stroke-width="1.6"/><ellipse cx="9" cy="9" rx="3.4" ry="7.5" fill="none" stroke="#fff" stroke-width="1.4"/><path d="M1.5 9 H16.5" stroke="#fff" stroke-width="1.4"/></svg></span>
  <span aria-label="Email"><svg width="18" height="14" viewBox="0 0 18 14"><rect x="1" y="1" width="16" height="12" fill="none" stroke="#fff" stroke-width="1.6"/><path d="M1 1 L9 8 L17 1" fill="none" stroke="#fff" stroke-width="1.6"/></svg></span>
  <span aria-label="Message"><svg width="18" height="17" viewBox="0 0 18 17"><path d="M2 1 H16 A1 1 0 0 1 17 2 V11 A1 1 0 0 1 16 12 H7 L3 16 V12 H2 A1 1 0 0 1 1 11 V2 A1 1 0 0 1 2 1 Z" fill="none" stroke="#fff" stroke-width="1.6"/></svg></span>
  <span aria-label="Link"><svg width="18" height="18" viewBox="0 0 18 18"><rect x="1.5" y="6" width="9" height="6" rx="3" fill="none" stroke="#fff" stroke-width="1.6" transform="rotate(-45 6 9)"/><rect x="7.5" y="6" width="9" height="6" rx="3" fill="none" stroke="#fff" stroke-width="1.6" transform="rotate(-45 12 9)"/></svg></span>
</div>
<div class="abs footer-rule"></div>
<p class="abs copyright">© Copyright 2017 Carla Winfield. All Rights Reserved</p>

</body>
</html>
```